To design a look and feel for a website. The company offers technical services to governemtns and public bodies. It does NOT market to the public.

The core business is GIS (Geographic Information Systems)

The site needs to be clean and simple, The current version is available here: www.velda-maps.ie

Thanks for your interest in our project

Target Market(s)

Goverment agencies and public bodies in the EU, buying through the public procurerment process

Requirements
Should not have
• corny graphics of hands holding globes or sateliites please.

```html
<!DOCTYPE html>
<html lang="en">
<head>
<meta charset="utf-8">
<title>The VELDA Group – Information Expertise</title>
<link href="https://fonts.googleapis.com/css2?family=Oswald:wght@400;500&family=Ubuntu:wght@400;500;700&display=swap" rel="stylesheet">
<style>
:root{
  --navy:#2b3d8f;
  --navy-dark:#1c2a66;
  --navy-deep:#152255;
  --lilac:#7a7ec4;
  --lilac-soft:#8f93cf;
  --label:#6c70b4;
  --text:#555a66;
  --page:#f5f5f5;
  --white:#ffffff;
  --rule:#d4d4d8;
}
*{margin:0;padding:0;box-sizing:border-box}
html,body{width:927px;height:1200px;overflow:hidden}
body{position:relative;background:var(--page);font-family:"Ubuntu",sans-serif;color:var(--text)}
.abs{position:absolute}

/* header */
.header{left:0;top:0;width:927px;height:94px;background:linear-gradient(#fff,#f7f7f7);border-top:3px solid var(--lilac)}
.brand{left:104px;top:30px;font-family:"Ubuntu",sans-serif;font-weight:500;font-size:26px;color:var(--navy);letter-spacing:1px;white-space:nowrap}
.brand small{font-size:12px;letter-spacing:0}
.tagline{left:106px;top:70px;font-size:10px;color:var(--lilac)}
.phone-tab{left:680px;top:0;width:143px;height:29px;background:linear-gradient(#8b8fd0,#6d71b8);border-radius:0 0 14px 14px;color:#fff;font-family:"Oswald",sans-serif;font-size:16px;display:flex;align-items:center;justify-content:center;gap:6px;white-space:nowrap}
.phone-tab svg{width:19px;height:19px}

/* nav */
.nav{left:0;top:94px;width:927px;height:30px;background:linear-gradient(#2c3d86,#1a2760);display:flex;padding-left:101px}
.nav a{display:flex;align-items:center;justify-content:center;color:#fff;text-decoration:none;font-size:13.5px;font-weight:500;border-right:1px solid #3b4a90;padding:0 13px}
.nav a.active{width:83px;background:linear-gradient(#8a8ec9,#5a5ea8)}

/* hero */
.hero{left:0;top:124px;width:927px;height:378px;background:
  radial-gradient(ellipse at 45% 55%,rgba(240,230,60,.85),rgba(240,230,60,0) 45%),
  radial-gradient(ellipse at 85% 40%,rgba(60,170,200,.7),rgba(60,170,200,0) 40%),
  linear-gradient(110deg,#3a3a12 0%,#8a8a1c 25%,#c8c030 45%,#5c7a22 70%,#1f4a5a 100%)}
.caption{left:0;top:455px;width:927px;height:47px;background:rgba(10,10,10,.72)}
.caption p{position:absolute;left:106px;top:5px;width:580px;color:#fff;font-size:14px;font-weight:500;line-height:19px}
.dots{left:727px;top:471px;display:flex;gap:6px}
.dots span{width:16px;height:16px;border-radius:50%;background:var(--lilac)}
.dots span.on{background:#fff}

/* section tabs */
.tab{width:111px;height:29px;background:linear-gradient(#6f73b9,#2b3575);border-radius:0 0 5px 5px;color:#fff;font-size:13px;font-weight:500;display:flex;align-items:center;justify-content:center;box-shadow:0 2px 3px rgba(0,0,0,.3);white-space:nowrap}

/* services */
.service{width:150px;text-align:center}
.service svg{width:84px;height:84px;display:block;margin:0 auto}
.service span{display:block;margin-top:9px;color:var(--label);font-size:13.5px;font-weight:500;white-space:nowrap}
.divider{left:101px;top:662px;width:726px;height:1px;background:var(--rule)}

/* about */
.h2{font-family:"Oswald",sans-serif;font-weight:400;font-size:17px;color:var(--navy)}
.about{left:115px;top:678px;width:472px}
.about p{font-size:9.2px;line-height:12.8px;margin-top:8px}
.about .h2{margin-bottom:-1px}

/* news */
.news{left:616px;top:676px;width:196px;height:227px;border:1px solid #cfcfd4;border-radius:4px;background:#f1f1f1;box-shadow:0 1px 2px rgba(0,0,0,.12);padding:6px 10px}
.news .h2{border-bottom:1px solid #cfcfd4;padding-bottom:3px;margin-bottom:8px}
.item{display:flex;gap:6px;height:45.5px}
.date{width:20px;height:22px;flex:none;border-radius:2px;overflow:hidden;font-size:7px;text-align:center;font-weight:700}
.date b{display:block;background:#8a8a90;color:#fff;height:9px;line-height:9px}
.date i{display:block;font-style:normal;background:#c9cbe6;color:var(--navy);height:13px;line-height:13px;font-size:9px}
.item p{font-size:8.8px;line-height:12.8px}
.item strong{color:#555;font-weight:500}
.view{font-family:"Oswald",sans-serif;font-size:10px;color:var(--navy)}

/* clients */
.clients-rule{left:120px;top:929px;width:690px;height:1px;background:linear-gradient(90deg,transparent,#cfcfd4,transparent)}
.arrow{width:28px;height:28px}
.client{top:970px;width:90px;height:30px;display:flex;align-items:center;justify-content:center;font-size:11.5px;font-weight:500;color:var(--navy);white-space:nowrap}

/* footer */
.footer{left:0;top:1036px;width:927px;height:141px;background:var(--navy);border-top:2px solid #4556a4}
.fh{font-family:"Oswald",sans-serif;font-weight:400;font-size:13px;color:#fff;white-space:nowrap}
.links{left:117px;top:1042px}
.links ul{list-style:none;margin-top:7px}
.links li{font-size:10.5px;color:#fff;height:21.8px}
.links li::before{content:"▪";color:var(--lilac-soft);font-size:7px;margin-right:5px;vertical-align:2px}
.contact{left:214px;top:1042px}
.map{left:214px;top:1070px;width:98px;height:97px;background:linear-gradient(135deg,#e9e6dc,#d9dccd 60%,#cbd5de)}
.ci{left:329px;display:flex;gap:10px;color:#fff;font-size:10.5px;line-height:14px;white-space:nowrap}
.ci svg{width:12px;height:12px;flex:none;margin-top:1px}
.newsletter{left:492px;top:1042px;width:160px}
.newsletter p{color:#fff;font-size:10.5px;line-height:14.5px;margin-top:6px}
.field{left:492px;top:1113px;width:145px;height:22px;background:#fff;border:1px solid #c8c8c8;font-size:9.5px;color:#888;padding:5px 6px;white-space:nowrap}
.submit{left:492px;top:1145px;width:66px;height:21px;background:linear-gradient(#8a8ec9,#5357a0);border-radius:3px;color:#fff;font-size:9.5px;font-weight:700;display:flex;align-items:center;justify-content:center}
.f-brand{left:668px;top:1070px;font-size:30px;font-weight:500;color:var(--lilac-soft);letter-spacing:1px}
.social{left:672px;top:1149px;display:flex;gap:12px}
.social span{color:#fff;font-size:10px;font-weight:500}
.copyright{left:0;top:1177px;width:927px;height:23px;background:var(--lilac);color:#fff;font-size:9.5px;display:flex;align-items:center;justify-content:center}
</style>
</head>
<body>

<header class="abs header"></header>
<div class="abs brand">THE VELDA <small>GROUP</small></div>
<div class="abs tagline">Information Expertise</div>
<div class="abs phone-tab">
  <svg viewBox="0 0 20 20"><circle cx="10" cy="10" r="8.5" fill="none" stroke="#fff" stroke-width="1.6"/><path d="M11.5 5.5c-3 .3-4.5 2.2-4.5 4.5s1.5 4.2 4.5 4.5" fill="none" stroke="#fff" stroke-width="2" stroke-linecap="round"/></svg>
  353 1 5550192
</div>

<nav class="abs nav">
  <a class="active">Home</a><a>Services</a><a>Clients</a><a>Contact</a><a>Inspire</a>
</nav>

<div class="abs hero" role="img" aria-label="Industrial skyline at night overlaid with glowing circuit lines and digital numbers"></div>
<div class="abs caption"><p>... we can help with spatial vector data. VELDA also has a strong experise in general data management.</p></div>
<div class="abs dots"><span class="on"></span><span></span><span></span><span></span></div>

<div class="abs tab" style="left:408px;top:496px">OUR SERVICES</div>

<div class="abs service" style="left:87px;top:539px">
  <svg viewBox="0 0 84 84"><circle cx="42" cy="42" r="41" fill="var(--navy)"/><circle cx="42" cy="42" r="37" fill="none" stroke="#fff" stroke-width="2"/>
    <g stroke="#fff" stroke-width="3" fill="none" stroke-linecap="round"><path d="M28 56l28-28"/><path d="M28 28l28 28"/><circle cx="27" cy="27" r="5"/><circle cx="57" cy="57" r="5"/></g></svg>
  <span>Data Management</span>
</div>
<div class="abs service" style="left:253px;top:539px">
  <svg viewBox="0 0 84 84"><circle cx="42" cy="42" r="41" fill="var(--navy)"/><circle cx="42" cy="42" r="37" fill="none" stroke="#fff" stroke-width="2"/>
    <circle cx="42" cy="42" r="15" fill="none" stroke="#fff" stroke-width="3"/><path d="M42 31l5 11-5 11-5-11z" fill="#fff"/></svg>
  <span>Spatial Data</span>
</div>
<div class="abs service" style="left:399px;top:539px">
  <svg viewBox="0 0 84 84"><circle cx="42" cy="42" r="41" fill="var(--navy)"/><circle cx="42" cy="42" r="37" fill="none" stroke="#fff" stroke-width="2"/>
    <path d="M14 56l18-22 8 8 9-13 21 27z" fill="#fff"/></svg>
  <span>Land Use</span>
</div>
<div class="abs service" style="left:545px;top:539px">
  <svg viewBox="0 0 84 84"><circle cx="42" cy="42" r="41" fill="var(--navy)"/><circle cx="42" cy="42" r="37" fill="none" stroke="#fff" stroke-width="2"/>
    <rect x="16" y="28" width="32" height="22" fill="#fff"/><path d="M50 34h10l7 8v8H50z" fill="#fff"/><circle cx="26" cy="53" r="5" fill="#fff" stroke="var(--navy)" stroke-width="2"/><circle cx="58" cy="53" r="5" fill="#fff" stroke="var(--navy)" stroke-width="2"/></svg>
  <span>Transport</span>
</div>
<div class="abs service" style="left:693px;top:539px">
  <svg viewBox="0 0 84 84"><circle cx="42" cy="42" r="41" fill="var(--navy)"/><circle cx="42" cy="42" r="37" fill="none" stroke="#fff" stroke-width="2"/>
    <circle cx="42" cy="30" r="8" fill="#fff"/><path d="M26 58c0-11 7-17 16-17s16 6 16 17z" fill="#fff"/></svg>
  <span>Consulting</span>
</div>

<div class="abs divider"></div>

<section class="abs about">
  <h2 class="h2">About Velda Group</h2>
  <p>The VELDA Group has been in business since 1994 and continues to develop and update its range of services. The company has a high level of expertise in handling data and information, and in building and re-engineering database systems. We have a particular expertise in working with Irish data sets and have a strong grounding in dealing with spatial data.</p>
  <p>We also have extensive experience in working in a Northwind development environment, both Desktop and WebForge. We have worked on development of small scale systems using Northwind products for over 12 years. We have assisted in the migration of systems from DeskBase to both QueryServer and Orion DB databases. This has included re-writing code from MacroScript to either VBX or CSX.</p>
  <p>We have built web sites for our clients using WebForge using CoreNet frameworks 1.5 through to 4.0. VELDA will work with all spatial data formats and systems including Orion DB, MapStudio, GeoSys QueryServer. We are not agents for any vendor, preferring to select the components that best suit the project's needs. The company's Quality Management System is ISO 9001:2008 certified (reviewed Jan 2012) The VELDA Group Ltd is registered in ireland number 415527</p>
</section>

<aside class="abs news">
  <h2 class="h2">Latest News</h2>
  <div class="item"><div class="date"><b>DEC</b><i>21</i></div><p><strong>Lorem ipsum dolor sit amet,</strong> consectetuer adipiscing elit, sed diam nonummy nibh euismod cidunt</p></div>
  <div class="item"><div class="date"><b>DEC</b><i>21</i></div><p><strong>Lorem ipsum dolor sit amet,</strong> consectetuer adipiscing elit, sed diam nonummy nibh euismod cidunt</p></div>
  <div class="item"><div class="date"><b>DEC</b><i>21</i></div><p><strong>Lorem ipsum dolor sit amet,</strong> consectetuer adipiscing elit, sed diam nonummy</p></div>
  <div class="item" style="height:33px"><div class="date"><b>DEC</b><i>21</i></div><p><strong>Lorem ipsum dolor sit amet,</strong> consectetuer adipiscing elit, sed</p></div>
  <div class="view">View more</div>
</aside>

<div class="abs clients-rule"></div>
<div class="abs tab" style="left:408px;top:927px">OUR CLIENTS</div>

<svg class="abs arrow" style="left:111px;top:968px" viewBox="0 0 28 28"><circle cx="14" cy="14" r="12.5" fill="#fff" stroke="#c9c9cd" stroke-width="2"/><path d="M16 9l-6 5 6 5z" fill="#b5b5ba"/></svg>
<div class="abs client" style="left:163px">Coach Line</div>
<div class="abs client" style="left:288px">Dept. of Farmland</div>
<div class="abs client" style="left:384px">Woodland Board</div>
<div class="abs client" style="left:472px">Health Board</div>
<div class="abs client" style="left:575px">Statbureau</div>
<div class="abs client" style="left:679px">World Council</div>
<svg class="abs arrow" style="left:790px;top:968px" viewBox="0 0 28 28"><circle cx="14" cy="14" r="12.5" fill="#fff" stroke="#c9c9cd" stroke-width="2"/><path d="M12 9l6 5-6 5z" fill="#b5b5ba"/></svg>

<footer class="abs footer"></footer>
<div class="abs links"><h3 class="fh">Quick Links</h3>
  <ul><li>Home</li><li>Services</li><li>Clients</li><li>Contact</li><li>Inspire</li></ul>
</div>
<div class="abs contact"><h3 class="fh">Contact Info</h3></div>
<div class="abs map" role="img" aria-label="Street map showing the office location"></div>
<div class="abs ci" style="top:1066px"><svg viewBox="0 0 12 12"><path d="M6 0.5a3.8 3.8 0 0 0-3.8 3.8C2.2 7 6 11.5 6 11.5S9.8 7 9.8 4.3A3.8 3.8 0 0 0 6 .5z" fill="var(--lilac-soft)"/><circle cx="6" cy="4.3" r="1.4" fill="var(--navy)"/></svg><span>Lorem ipsum dolor<br>sit amet consectetuer,</span></div>
<div class="abs ci" style="top:1105px"><svg viewBox="0 0 12 12"><path d="M2.5 1l2 2.5-1.2 1.3c.8 1.6 2 2.8 3.6 3.6L8.2 7.2 10.8 9.2 9.5 11C5 10.5 1.5 7 1 2.5z" fill="var(--lilac-soft)"/></svg><span>+ 353 1 5550192</span></div>
<div class="abs ci" style="top:1131px"><svg viewBox="0 0 12 12"><rect x="2" y="1" width="8" height="5" fill="none" stroke="var(--lilac-soft)" stroke-width="1.2"/><rect x="1" y="6" width="10" height="5" fill="var(--lilac-soft)"/></svg><span>+ 353 1 5550193</span></div>
<div class="abs ci" style="top:1155px"><svg viewBox="0 0 12 12"><rect x="1" y="2.5" width="10" height="7" fill="var(--lilac-soft)"/><path d="M1 2.5l5 4 5-4" fill="none" stroke="var(--navy)" stroke-width="1"/></svg><span>contact@velda-maps.ie</span></div>

<div class="abs newsletter"><h3 class="fh">Newsletter</h3>
  <p>Lorem ipsum dolor sit amet, consectetuer adipiscing elit, sed diam nonummy nibh</p>
</div>
<div class="abs field">Enter your e-mail address</div>
<div class="abs submit">SUBMIT</div>

<div class="abs f-brand">VELDA</div>
<div class="abs social"><span>Friendbook</span><span>Chirper</span><span>Linkup</span></div>

<div class="abs copyright">© 2013 velda-maps.ie. &nbsp;|&nbsp; All right reserved.</div>

</body>
</html>
```